holloway paving service

Needs to have phone number 0418259730 and email markholloway@brightmail.com.au.
ABN 62318470915
name mark holloway

For all your concreting solutions
Excavation
Exposed & colour concrete
House & shed slabs
Driveways
Landing & steps

Contact Information for Business Card

ph 0418259730
email markholloway@brightmail.com.au.
ABN 62318470915
name mark holloway

```html
<!DOCTYPE html>
<html lang="en">
<head>
<meta charset="utf-8">
<title>Holloway Paving Service – Business Card</title>
<link rel="stylesheet" href="https://fonts.googleapis.com/css2?family=Roboto:wght@400;500;700&family=Roboto+Condensed:wght@500;700&display=swap">
<style>
  :root {
    --page-bg: #e4e1dd;
    --card-light: #f1f0ee;
    --card-light-edge: #e2e1df;
    --brand-orange: #e0532e;
    --brand-dark: #4a4a4c;
    --divider: #3a3634;
    --panel-red-top: #d7401c;
    --panel-red-bottom: #c4331a;
    --panel-text: #f6e4d8;
    --panel-name: #f3d9c6;
  }
  * { box-sizing: border-box; margin: 0; padding: 0; }
  html, body { width: 1200px; height: 969px; overflow: hidden; }
  body {
    background: var(--page-bg);
    font-family: "Roboto", Arial, sans-serif;
    position: relative;
  }
  .business-card {
    position: absolute;
    left: 100px; top: 200px;
    width: 1000px; height: 570px;
    background: linear-gradient(135deg, var(--card-light), var(--card-light-edge));
    box-shadow: 0 10px 30px rgba(0,0,0,0.18);
    overflow: hidden;
  }
  .card-front { position: absolute; inset: 0 466px 0 0; }
  .brand-square {
    position: absolute; left: 82px; top: 232px;
    width: 70px; height: 70px;
    background: var(--brand-orange);
  }
  .brand-rule {
    position: absolute; left: 186px; top: 222px;
    width: 3px; height: 112px;
    background: var(--brand-orange);
  }
  .brand-name {
    position: absolute; left: 202px; top: 232px;
    font-family: "Roboto Condensed", Arial, sans-serif;
    font-weight: 700; font-size: 25px; line-height: 30px;
    color: var(--brand-orange);
    letter-spacing: 0.5px;
  }
  .brand-phone {
    position: absolute; left: 202px; top: 300px;
    font-family: "Roboto Condensed", Arial, sans-serif;
    font-weight: 500; font-size: 20px;
    color: var(--brand-orange);
    letter-spacing: 2px;
  }
  .card-divider {
    position: absolute; left: 530px; top: 0;
    width: 6px; height: 100%;
    background: var(--divider);
  }
  .card-details {
    position: absolute; left: 536px; top: 0; right: 0; bottom: 0;
    background: linear-gradient(160deg, var(--panel-red-top), var(--panel-red-bottom));
    color: var(--panel-text);
  }
  .divider-mark {
    position: absolute; left: 516px; top: 96px;
    width: 34px; height: 34px;
    background: var(--brand-orange);
    border: 3px solid var(--card-light);
  }
  .holder-name {
    position: absolute; left: 54px; top: 92px;
    font-family: "Roboto Condensed", Arial, sans-serif;
    font-weight: 500; font-size: 36px;
    color: var(--panel-name);
    text-transform: uppercase;
    letter-spacing: 0.5px;
  }
  .contact-list, .service-list { position: absolute; left: 66px; list-style: none; }
  .contact-list { top: 172px; }
  .contact-item, .service-item {
    display: flex; align-items: center;
    font-size: 23px; height: 32px;
  }
  .contact-icon { width: 18px; height: 18px; margin-right: 14px; fill: var(--panel-text); }
  .abn-line { position: absolute; left: 66px; top: 278px; font-size: 23px; letter-spacing: 0.5px; }
  .service-list { top: 322px; }
  .service-item::before {
    content: ""; width: 8px; height: 8px; margin: 0 16px 0 4px;
    background: var(--panel-text); transform: rotate(45deg);
  }
</style>
</head>
<body>
  <section class="business-card">
    <div class="card-front">
      <div class="brand-square"></div>
      <div class="brand-rule"></div>
      <p class="brand-name">HOLLOWAY PAVING<br>SERVICE</p>
      <p class="brand-phone">0418259730</p>
    </div>
    <div class="card-divider"></div>
    <div class="card-details">
      <h1 class="holder-name">Mark Holloway</h1>
      <ul class="contact-list">
        <li class="contact-item">
          <svg class="contact-icon" viewBox="0 0 24 24"><path d="M6.6 10.8a15.1 15.1 0 0 0 6.6 6.6l2.2-2.2a1 1 0 0 1 1-.25 11.4 11.4 0 0 0 3.6.57 1 1 0 0 1 1 1V20a1 1 0 0 1-1 1A17 17 0 0 1 3 4a1 1 0 0 1 1-1h3.5a1 1 0 0 1 1 1c0 1.25.2 2.45.57 3.57a1 1 0 0 1-.25 1z"/></svg>
          0418259730
        </li>
        <li class="contact-item">
          <svg class="contact-icon" viewBox="0 0 24 24"><path d="M2 5h20v14H2z M3.5 6.5 12 12l8.5-5.5" fill="none" stroke="#f6e4d8" stroke-width="0"/><path d="M2 5h20v2l-10 6L2 7z M2 9l10 6 10-6v10H2z"/></svg>
          markholloway@brightmail.com.au
        </li>
        <li class="contact-item">
          <svg class="contact-icon" viewBox="0 0 24 24"><circle cx="12" cy="12" r="10"/><path d="M7 7c2 1 3 3 2 5s-3 2-2 5M15 5c-1 2 1 3 2 4s2 3 0 5-1 4-2 5" fill="none" stroke="#cf3a1b" stroke-width="1.6"/></svg>
          www.hollowaypaving.com.au
        </li>
      </ul>
      <p class="abn-line">ABN 62318470915</p>
      <ul class="service-list">
        <li class="service-item">Excavation</li>
        <li class="service-item">Exposed &amp; colour concrete</li>
        <li class="service-item">House &amp; shed slabs</li>
        <li class="service-item">Driveways</li>
        <li class="service-item">Landing &amp; steps</li>
      </ul>
    </div>
    <div class="divider-mark"></div>
  </section>
</body>
</html>
```